Kindle Your Clients Book Cover

A book main title will be, "Kindle Your Clients"
The subtext will be, "Go to market with a story that sizzles"
Would like it to blend with my web site brand. You can find it here: www.kindleyourclients.example

Audience is business and revenue leaders for small, medium and large businesses. They have a new solution, or want to enter a new market, and they need to "inspire their buyers" meaning getting the buyers to want to change enough to overcome their status quo bias. They need a story that sizzles to do this.

```html
<!DOCTYPE html>
<html lang="en">
<head>
<meta charset="utf-8">
<title>Kindle Your Clients – Book Cover Wrap</title>
<link href="https://fonts.googleapis.com/css2?family=Montserrat:ital,wght@0,500;0,600;0,700;1,700&display=swap" rel="stylesheet">
<style>
  :root{
    --stage:#2b2b2b;
    --back-top:#0781b7;
    --back-bottom:#0a8ec6;
    --front-light:#18b0e2;
    --front-mid:#0d97cf;
    --front-deep:#0a88c0;
    --spine:#0883ba;
    --ink:#ffffff;
    --art-light:#e9eef2;
    --art-shade:#c3cdd5;
    --shadow-deep:#1a6f98;
    --shadow-soft:#0c8cc4;
  }
  *{margin:0;padding:0;box-sizing:border-box}
  html,body{width:1200px;height:1200px;overflow:hidden;background:var(--stage)}
  body{font-family:"Montserrat",sans-serif;color:var(--ink)}

  .cover-wrap{
    position:absolute;left:40px;top:206px;width:1120px;height:788px;
    display:flex;
  }

  /* Back cover */
  .back-cover{
    width:526px;height:100%;position:relative;
    background:linear-gradient(180deg,var(--back-top),var(--back-bottom));
  }
  .back-heading{
    position:absolute;left:0;right:0;top:52px;text-align:center;
    font-weight:700;font-size:27px;letter-spacing:-1px;
  }
  .back-heading em{font-style:italic}
  .blurb{
    position:absolute;left:51px;width:425px;top:104px;
    font-weight:500;font-size:11.6px;line-height:15.85px;text-align:justify;
  }
  .blurb p{margin-bottom:15.85px}

  /* Spine */
  .spine{
    width:68px;height:100%;position:relative;
    background:linear-gradient(180deg,var(--spine),var(--back-bottom));
    border-left:1px solid rgba(255,255,255,.05);
    border-right:1px solid rgba(0,60,100,.12);
  }
  .spine-text{
    position:absolute;top:56px;left:50%;transform:translateX(-50%);
    writing-mode:vertical-rl;white-space:nowrap;
    font-weight:600;font-size:33px;letter-spacing:-1.2px;line-height:1;
  }
  .spine-text em{font-style:italic;font-weight:700}
  .spine-gap{display:inline-block;height:38px}

  /* Front cover */
  .front-cover{
    width:526px;height:100%;position:relative;overflow:hidden;
    background:
      radial-gradient(ellipse at 95% 0%,var(--front-light),transparent 60%),
      linear-gradient(180deg,var(--front-mid),var(--front-deep));
  }
  .front-title{
    position:absolute;left:42px;top:50px;
    font-weight:700;line-height:.96;letter-spacing:-4px;
  }
  .front-title .line{display:block;font-size:100px}
  .front-title .line-accent{font-style:italic;font-size:90px;letter-spacing:-4px}
  .plane-art{
    position:absolute;left:124px;top:377px;width:260px;height:90px;
    border-radius:6px;
    background:linear-gradient(160deg,var(--art-light),var(--art-shade));
  }
  .tagline{
    position:absolute;left:0;right:0;top:488px;text-align:center;
    font-weight:600;font-size:20px;letter-spacing:-.3px;
  }
  .shadow-art{
    position:absolute;left:139px;top:531px;width:250px;height:117px;
    border-radius:6px;
    background:linear-gradient(160deg,var(--shadow-deep),var(--shadow-soft));
  }
  .author{
    position:absolute;left:0;right:0;top:690px;text-align:center;
    font-weight:600;font-size:56px;letter-spacing:-1.5px;line-height:1;
  }
</style>
</head>
<body>
<main class="cover-wrap">
  <section class="back-cover">
    <h2 class="back-heading">KINDLE YOUR <em>CLIENTS</em></h2>
    <div class="blurb">
      <p>Lorem ipsum dolor sit amet, consectetur adipiscing elit, sed do eiusmod tempor incididunt ut labore et dolore magna aliqua. Quis ipsum suspendisse ultrices gravida. Risus commodo viverra maecenas accumsan lacus vel facilisis. Lorem ipsum dolor sit amet, consectetur adipiscing elit, sed do eiusmod tempor incididunt ut labore et dolore magna aliqua. Quis ipsum suspendisse ultrices gravida. Risus commodo viverra maecenas accumsan lacus vel facilisis. Lorem ipsum dolor sit amet, consectetur adipiscing elit, sed do eiusmod tempor incididunt ut labore et dolore magna aliqua. Quis ipsum suspendisse ultrices gravida. Risus commodo viverra maecenas accumsan lacus vel facilisis.</p>
      <p>Lorem ipsum dolor sit amet, consectetur adipiscing elit, sed do eiusmod tempor incididunt ut labore et dolore magna aliqua. Quis ipsum suspendisse ultrices gravida. Risus commodo viverra maecenas accumsan lacus vel facilisis. Lorem ipsum dolor sit amet, consectetur adipiscing elit, sed do eiusmod tempor incididunt ut labore et dolore magna aliqua. Quis ipsum suspendisse ultrices gravida. Risus commodo viverra maecenas accumsan lacus vel facilisis. Lorem ipsum dolor sit amet, consectetur adipiscing elit, sed do eiusmod tempor incididunt ut labore et dolore magna aliqua. Quis ipsum suspendisse ultrices gravida. Risus commodo viverra maecenas accumsan lacus vel facilisis. Lorem ipsum dolor sit amet, consectetur adipiscing elit, sed do eiusmod tempor incididunt ut labore et dolore magna aliqua. Quis ipsum suspendisse ultrices gravida. Risus commodo viverra maecenas accumsan lacus vel facilisis.</p>
      <p>Lorem ipsum dolor sit amet, consectetur adipiscing elit, sed do eiusmod tempor incididunt ut labore et dolore magna aliqua. Quis ipsum suspendisse ultrices gravida. Risus commodo viverra maecenas accumsan lacus vel facilisis. Lorem ipsum dolor sit amet, consectetur adipiscing elit, sed do eiusmod tempor incididunt ut labore et dolore magna aliqua. Quis ipsum suspendisse ultrices gravida. Risus commodo viverra maecenas accumsan lacus vel facilisis. Lorem ipsum dolor sit amet, consectetur adipiscing elit, sed do eiusmod tempor incididunt ut labore et dolore magna aliqua. Quis ipsum suspendisse ultrices gravida. Risus commodo viverra maecenas accumsan lacus vel facilisis.</p>
    </div>
  </section>

  <section class="spine">
    <div class="spine-text">KINDLE YOUR <em>CLIENTS</em><span class="spine-gap"></span>AUTHOR NAME</div>
  </section>

  <section class="front-cover">
    <h1 class="front-title">
      <span class="line">KINDLE</span>
      <span class="line">YOUR</span>
      <span class="line line-accent">CLIENTS</span>
    </h1>
    <div class="plane-art" role="img" aria-label="Photo of a white folded paper airplane in flight"></div>
    <p class="tagline">Go to market with a story that sizzles</p>
    <div class="shadow-art" role="img" aria-label="Photo of the blurred shadow of a jet airliner cast below the paper airplane"></div>
    <p class="author">AUTHOR NAME</p>
  </section>
</main>
</body>
</html>
```